Business Card Design for Marketing Firm

Looking for business card design for higher end marketing firm. Clean but impressionable/trendy. We are a marketing firm that represents manufacturers in the foodservice equipment and supply industry. Our customers are end users such has hotels, restaurants, country clubs, convention centers and casinos as well as distributors of restaurants supplies and equipment, and manufacturers of foodservice equipment and supplies.
Target Market(s)
Hotels, Restaurants, Supply & Equipment Distributors, Foodservice Manufacturers
Industry/Entity Type
Foodservice/Hospitality
Contact Information for Business Card
Name, Title, Contact Number, Email, Website, Social Media, Address
Requirements
Must have
- Clean & Simple but Serious and Impressionable

```html
<!DOCTYPE html>
<html lang="en">
<head>
<meta charset="utf-8">
<title>Harbor Foodservice Reps – Business Card</title>
<link href="https://fonts.googleapis.com/css2?family=Cinzel:wght@600&family=Poppins:wght@400&display=swap" rel="stylesheet">
<style>
  :root {
    --backdrop: #2c2c2e;
    --card-white: #ffffff;
    --navy: #000080;
    --ink: #111111;
    --ink-soft: #333333;
    --divider: #b5b5b5;
  }
  html, body {
    margin: 0;
    padding: 0;
    width: 1093px;
    height: 1200px;
    overflow: hidden;
    background: var(--backdrop);
  }
  .canvas {
    position: relative;
    width: 1093px;
    height: 1200px;
  }
  .card {
    position: absolute;
    left: 265px;
    width: 578px;
    height: 356px;
    border-radius: 27px;
    overflow: hidden;
  }
  .card--front { top: 226px; background: var(--card-white); }
  .card--back  { top: 621px; background: var(--navy); }

  /* Front: brand block */
  .brand {
    position: absolute;
    left: 36px;
    width: 236px;
    top: 120px;
    text-align: center;
    color: var(--navy);
  }
  .brand__dot {
    display: block;
    width: 44px;
    height: 44px;
    margin: 0 auto 14px;
    border-radius: 50%;
    background: var(--navy);
  }
  .brand__name {
    font-family: "Cinzel", serif;
    font-weight: 600;
    font-size: 18px;
    line-height: 1.2;
    letter-spacing: 0.3px;
    text-transform: uppercase;
    margin: 0;
  }
  .divider {
    position: absolute;
    left: 288px;
    top: 75px;
    width: 1.5px;
    height: 208px;
    background: linear-gradient(var(--divider), #8a8a8a, var(--divider));
  }

  /* Front: contact block */
  .contact {
    position: absolute;
    left: 311px;
    top: 90px;
    font-family: "Poppins", sans-serif;
    color: var(--ink);
  }
  .contact__name {
    font-family: "Cinzel", serif;
    font-weight: 600;
    font-size: 23px;
    color: var(--navy);
    text-transform: uppercase;
    margin: 0;
    line-height: 1;
  }
  .contact__title {
    font-size: 17px;
    color: var(--ink-soft);
    margin: 0 0 11px;
    line-height: 1.2;
  }
  .contact__list {
    list-style: none;
    margin: 0;
    padding: 0;
  }
  .contact__item {
    display: flex;
    align-items: center;
    gap: 7px;
    font-size: 17px;
    line-height: 21px;
  }
  .contact__icon {
    width: 15px;
    height: 15px;
    flex: none;
  }
  .contact__highlight { color: var(--navy); }
  .contact__address {
    font-size: 17px;
    line-height: 21px;
    margin: 12px 0 0;
    font-style: normal;
  }

  /* Back */
  .back-brand {
    position: absolute;
    left: 0;
    right: 0;
    top: 86px;
    text-align: center;
    color: var(--card-white);
  }
  .back-brand__dot {
    display: block;
    width: 92px;
    height: 92px;
    margin: 0 auto 28px;
    border-radius: 50%;
    background: var(--card-white);
  }
  .back-brand__name {
    font-family: "Cinzel", serif;
    font-weight: 600;
    font-size: 27px;
    line-height: 1.15;
    letter-spacing: 0.4px;
    text-transform: uppercase;
    margin: 0;
  }
  .socials {
    position: absolute;
    left: 0;
    right: 0;
    top: 300px;
    display: flex;
    justify-content: center;
    gap: 7px;
  }
  .socials__circle {
    width: 30px;
    height: 30px;
    border: 1.5px solid var(--card-white);
    border-radius: 50%;
  }
</style>
</head>
<body>
<main class="canvas">

  <section class="card card--front" aria-label="Business card front">
    <div class="brand">
      <span class="brand__dot"></span>
      <p class="brand__name">Harbor Foodservice<br>Reps</p>
    </div>

    <div class="divider"></div>

    <div class="contact">
      <h1 class="contact__name">Daniel Brooks</h1>
      <p class="contact__title">Managing Director</p>
      <ul class="contact__list">
        <li class="contact__item">
          <svg class="contact__icon" viewBox="0 0 24 24" aria-hidden="true"><path fill="#000080" d="M6.6 10.8a15.1 15.1 0 0 0 6.6 6.6l2.2-2.2a1 1 0 0 1 1-.25 11.4 11.4 0 0 0 3.6.57 1 1 0 0 1 1 1V20a1 1 0 0 1-1 1A17 17 0 0 1 3 4a1 1 0 0 1 1-1h3.5a1 1 0 0 1 1 1c0 1.25.2 2.45.57 3.57a1 1 0 0 1-.25 1z"/></svg>
          055-987 654 321
        </li>
        <li class="contact__item">
          <svg class="contact__icon" viewBox="0 0 24 24" aria-hidden="true"><path fill="#000080" d="M2 5h20v14H2z"/><path fill="none" stroke="#fff" stroke-width="1.6" d="M2.5 5.5 12 13l9.5-7.5M2.5 18.5l7-6.5M21.5 18.5l-7-6.5"/></svg>
          hello@harborreps.com
        </li>
        <li class="contact__item">
          <svg class="contact__icon" viewBox="0 0 24 24" aria-hidden="true"><g fill="none" stroke="#000080" stroke-width="1.8"><circle cx="12" cy="12" r="10"/><ellipse cx="12" cy="12" rx="4.5" ry="10"/><path d="M2 12h20M4 7h16M4 17h16"/></g></svg>
          <span>www.<span class="contact__highlight">harborreps</span>.com</span>
        </li>
      </ul>
      <address class="contact__address">88, Quayside Road, Suite 12<br>60614,Northland</address>
    </div>
  </section>

  <section class="card card--back" aria-label="Business card back">
    <div class="back-brand">
      <span class="back-brand__dot"></span>
      <p class="back-brand__name">Harbor Foodservice<br>Reps</p>
    </div>
    <div class="socials" aria-label="Social media">
      <span class="socials__circle"></span>
      <span class="socials__circle"></span>
      <span class="socials__circle"></span>
    </div>
  </section>

</main>
</body>
</html>
```